Recruitment of Trellan Staffing for the UK market

I want a website for the UK market to attract businesses and companies to come to us for Philipine labour. We want an information site that gives all information on what we do and how we can recruit Philippine labour.
This is a recruitment site for companies to contact us with their requirements for skilled workers coming from the Philipines over to the UK to work.

Target Market(s)

Uk Companies and businesses who want Philipine skilled workers

Industry/Entity Type

REcruitment

Coding

Number of Pages Required

5+ page

Font styles to use
Sans Serif

Colors
0054AA
0677BA
7BADD7
CADEEF
E8F1F8
0094D4
00A9DD
6FCCEA
C7EBF8
E9F6FB
EE7325
F08F49
F5BC92
FAE3D3
FDF4ED
EB3D1F
EC4F4E
F09395
F8D3D4
FCEDEE

Requirements
Must have
• Look professional and corperate with drop down menus for Home ,about, services,articles. training , contact us
Nice to have
• Look at Velmora recruitment- https://velmorarecruitment.example.co.uk/. This is my current site - https://www.trellanstaffing.example.com/
Should not have
• Cartoons or silly pictures , needs to be corperate looking

```html
<!DOCTYPE html>
<html lang="en">
<head>
<meta charset="utf-8">
<title>Trellan Staffing — Philippine Skilled Workers for UK Companies</title>
<link href="https://fonts.googleapis.com/css2?family=Montserrat:wght@400;500;600;700;800&display=swap" rel="stylesheet">
<style>
:root{
  --blue:#0054aa;
  --blue-mid:#0677ba;
  --blue-soft:#7badd7;
  --blue-pale:#cadeef;
  --blue-mist:#e8f1f8;
  --orange:#ee7325;
  --orange-soft:#f5bc92;
  --orange-pale:#fae3d3;
  --red:#eb3d1f;
  --ink:#111;
  --text:#333;
  --muted:#8a8a8a;
  --grey-bg:#f1f1f1;
  --line:#d9d9d9;
  --dark:#2b2b2b;
}
*{box-sizing:border-box;margin:0;padding:0}
html,body{width:1200px;height:5236px;overflow:hidden}
body{font-family:'Montserrat',sans-serif;color:var(--text);background:#fff;position:relative}
section,header,footer{position:absolute;left:0;width:1200px}
.abs{position:absolute}
.btn{position:absolute;display:flex;align-items:center;justify-content:center;background:var(--blue);color:#fff;font-size:12px;font-weight:600;text-decoration:none}
.btn.orange{background:var(--orange)}
.btn.white{background:#fff;color:var(--blue)}
.rule{width:36px;height:3px;background:var(--orange);margin:14px 0 20px}
.img-fill{position:absolute}

/* header */
.site-header{top:0;height:80px}
.brand{position:absolute;left:163px;top:22px;display:flex;align-items:center;gap:10px;font-size:20px;font-weight:700;color:var(--blue)}
.brand .mark{width:28px;height:28px;border-radius:50%;background:var(--orange)}
.main-nav{position:absolute;right:160px;top:30px;display:flex;gap:36px;font-size:13px;color:var(--ink)}
.main-nav a{color:inherit;text-decoration:none}
.main-nav a.active{color:var(--blue-mid)}

/* hero */
.hero{top:80px;height:400px}
.social-rail{position:absolute;left:70px;top:100px;display:flex;flex-direction:column;align-items:center;gap:12px}
.social-rail .dot{width:12px;height:12px;border-radius:50%;border:2px solid var(--orange)}
.social-rail .dot.solid{width:28px;height:28px;background:var(--orange);border:none}
.social-rail .label{writing-mode:vertical-rl;transform:rotate(180deg);font-size:11px;color:var(--muted)}
.social-rail .arrow{width:1px;height:40px;background:var(--muted)}
.hero-title{position:absolute;left:163px;top:92px;font-size:33px;line-height:43px;font-weight:800;color:var(--ink);text-transform:uppercase}
.hero-title .accent{color:var(--orange)}
.hero-art{left:590px;top:0;width:490px;height:398px;background:linear-gradient(160deg,var(--blue-pale),#f2a15c 55%,var(--orange))}

/* inquiry */
.inquiry{position:absolute;left:161px;top:476px;width:878px;height:187px;background:var(--blue);border-radius:4px;box-shadow:0 10px 24px rgba(0,84,170,.25)}
.inquiry h2{text-align:center;color:#fff;font-size:26px;font-weight:500;margin-top:18px}
.inquiry .title-line{position:absolute;left:40px;right:40px;top:60px;height:1px;background:rgba(255,255,255,.25)}
.field{position:absolute;background:var(--blue-pale);color:#333;font-size:12px;padding:10px 18px;border-radius:2px}
.inquiry .submit{position:absolute;left:748px;top:78px;width:88px;height:84px;background:var(--orange);color:#fff;font-weight:800;font-size:15px;display:flex;align-items:center;justify-content:center;text-align:center;line-height:18px}

/* about */
.about{top:728px;height:537px;background:var(--grey-bg)}
.about .circle-shadow{left:450px;top:320px;width:110px;height:110px;border-radius:50%;background:#d9d9d9}
.about .photo{left:161px;top:53px;width:392px;height:392px;border-radius:50%;background:linear-gradient(135deg,#dfe4ea,#9aa7b6 60%,#4a5a70);border:6px solid #fff}
.section-title{font-size:31px;font-weight:600;color:var(--ink);line-height:38px}
.about .copy{position:absolute;left:632px;top:120px;width:400px}
.copy p{font-size:12px;line-height:23px;color:var(--text)}

/* working together */
.working{top:1265px;height:538px}
.working .copy{position:absolute;left:163px;top:133px;width:360px}
.working .copy p{font-size:16px;line-height:34px}
.working .red{color:var(--red);font-weight:700;text-decoration:underline}
.working .map{left:630px;top:56px;width:387px;height:386px;background:radial-gradient(ellipse at 55% 45%,var(--blue-pale),var(--blue-mist) 70%,#fff)}

/* cards */
.offer{top:1803px;height:545px;background:var(--grey-bg)}
.offer-card{position:absolute;top:91px;width:259px;height:289px;background:#fff;text-align:center;box-shadow:0 2px 8px rgba(0,0,0,.05)}
.offer-card .icon{width:86px;height:86px;margin:34px auto 18px;border:3px solid var(--blue);border-radius:12px;position:relative}
.offer-card .icon::after{content:"";position:absolute;left:24px;top:24px;width:32px;height:32px;border:3px solid var(--orange);border-radius:50%}
.offer-card h3{font-size:16px;font-weight:600;color:var(--ink);margin-bottom:14px}
.offer-card p{font-size:11.5px;line-height:23px;padding:0 28px}

/* placement */
.placement{top:2348px;height:559px}
.center-title{position:absolute;left:0;width:1200px;text-align:center;font-size:31px;font-weight:600;color:var(--ink)}
.center-title::after{content:"";display:block;width:36px;height:3px;background:var(--orange);margin:14px auto 0}
.tile{position:absolute;top:164px;width:272px;height:228px;display:flex;align-items:center;justify-content:center;color:#fff;font-size:20px;font-weight:700;text-shadow:0 2px 4px rgba(0,0,0,.5)}
.slider-arrow{position:absolute;top:258px;width:42px;height:41px;border:1px solid var(--line);background:#fff;display:flex;align-items:center;justify-content:center}

/* testimonial */
.testimonial{top:2907px;height:488px;background:var(--grey-bg)}
.testimonial .photo{left:161px;top:112px;width:325px;height:264px;background:linear-gradient(135deg,#c9d0d8,#6f7c8c 55%,#2f3b4a)}
.quote-card{position:absolute;left:439px;top:89px;width:598px;height:307px;background:#fff;padding:30px 0 0 104px}
.stars{color:var(--orange);font-size:22px;letter-spacing:2px}
.quote-card p{font-size:14px;line-height:28px;margin-top:10px;width:430px}
.quote-card .name{font-size:16px;font-weight:600;color:var(--blue);margin-top:42px}
.quote-card .role{font-size:11px;color:var(--muted)}
.quote-card .qmark{position:absolute;right:36px;bottom:-26px;font-size:110px;font-weight:800;color:var(--orange-pale);line-height:1}

/* articles */
.articles{top:3395px;height:453px}
.article-card{position:absolute;top:128px;width:270px;height:236px;border:1px solid var(--line);text-align:center;padding-top:60px}
.article-card .badge{position:absolute;left:50%;top:-32px;margin-left:-34px;width:68px;height:68px;border-radius:50%;background:#fff;border:1px solid var(--line)}
.article-card .badge::after{content:"";position:absolute;left:20px;top:18px;width:28px;height:32px;border:2px solid var(--blue);border-radius:3px}
.article-card h3{font-size:16px;font-weight:600;color:var(--ink);margin-bottom:12px}
.article-card p{font-size:11.5px;line-height:23px;padding:0 20px;height:72px}
.article-card .btn{position:static;width:114px;height:36px;margin:14px auto 0}

/* contact band */
.contact-band{top:3848px;height:451px;background:linear-gradient(90deg,#232323 0%,#2e2e2e 45%,#3b3a36 100%)}
.contact-band .photo{left:590px;top:0;width:610px;height:451px;background:linear-gradient(120deg,rgba(60,60,60,0),#3b5c9a 45%,#d46a2a 70%,#2a3d70)}
.contact-band .copy{position:absolute;left:163px;top:100px;width:400px;color:#fff}
.contact-band h2{font-size:31px;font-weight:600;color:#fff}
.contact-band .rule{background:#fff;margin:12px 0 16px}
.contact-band p{font-size:12px;line-height:23px;color:#eee}

/* quick contact */
.quick-contact{top:4299px;height:600px}
.qc-field{position:absolute;width:290px;height:60px;border-bottom:1px solid #bbb}
.qc-field .lbl{font-size:10px;color:var(--muted)}
.qc-field .val{font-size:11px;color:var(--ink);margin-top:12px}
.qc-field svg{position:absolute;right:4px;top:24px}

/* footer */
.site-footer{top:4899px;height:294px;background:var(--blue);color:#fff}
.site-footer h4{font-size:15px;font-weight:600}
.site-footer .rule{background:var(--orange);width:30px;height:2px;margin:10px 0 14px}
.foot-col{position:absolute;top:76px}
.links{display:grid;grid-template-columns:105px 105px;row-gap:20px;font-size:12px}
.contact-list{font-size:12px;line-height:18px}
.contact-list div{display:flex;gap:10px;margin-bottom:12px}
.socials{display:flex;gap:7px}
.socials span{width:27px;height:27px;border-radius:50%;border:1.5px solid #fff}
.foot-brand{display:flex;align-items:center;gap:8px;font-size:18px;font-weight:700;margin-top:26px}
.foot-brand .mark{width:22px;height:22px;background:#fff;border-radius:50%}
.legal{position:absolute;top:5193px;left:0;width:1200px;height:43px;background:var(--orange);color:#fff;font-size:11px;display:flex;align-items:center;justify-content:center}
</style>
</head>
<body>

<header class="site-header">
  <div class="brand"><span class="mark"></span>Trellan Staffing</div>
  <nav class="main-nav">
    <a class="active" href="#">Home</a><a href="#">About</a><a href="#">Services</a><a href="#">Articles</a><a href="#">Training</a><a href="#">Contact Us</a>
  </nav>
</header>

<section class="hero">
  <div class="social-rail">
    <span class="dot"></span><span class="dot solid"></span><span class="dot"></span><span class="dot"></span>
    <span class="label">scroll</span><span class="arrow"></span>
  </div>
  <h1 class="hero-title">Recruiting and<br>placing skilled<br><span class="accent">Philippine workers</span><br>into UK companies</h1>
  <a class="btn orange" href="#" style="left:161px;top:280px;width:166px;height:36px">Contact Us Today</a>
  <div class="img-fill hero-art" role="img" aria-label="Two Philippine engineers in orange hard hats and safety vests holding plans"></div>
  <form class="inquiry">
    <h2>Quick Inquiry</h2>
    <div class="title-line"></div>
    <div class="field" style="left:43px;top:78px;width:225px;height:37px">First name*</div>
    <div class="field" style="left:278px;top:78px;width:225px;height:37px">Last name*</div>
    <div class="field" style="left:43px;top:125px;width:225px;height:37px">Phone*</div>
    <div class="field" style="left:278px;top:125px;width:225px;height:37px">Email*</div>
    <div class="field" style="left:514px;top:78px;width:224px;height:84px">Message</div>
    <div class="submit">SUBMIT<br>NOW</div>
  </form>
</section>

<section class="about">
  <div class="img-fill circle-shadow"></div>
  <div class="img-fill photo" role="img" aria-label="Two businessmen reviewing work at a laptop in a bright office"></div>
  <div class="copy">
    <h2 class="section-title">What The Business<br>is About</h2>
    <div class="rule"></div>
    <p>We source skilled workers directly from the Philippines to work in the UK. With offices , training locations and specialist recruiters we can find the highest quality individuals to add value and resources to any UK buisness. We delivery quality based on vast experience over a number of years.</p>
    <a class="btn" href="#" style="top:292px;left:0;width:113px;height:36px">Contact Us</a>
  </div>
</section>

<section class="working">
  <div class="copy">
    <h2 class="section-title">Working Together</h2>
    <div class="rule"></div>
    <p>We recruit the finest talent available with our dedicated 200 strong team.<br>Our centres are highlighted in <span class="red">Red Dots</span> on the map.</p>
    <a class="btn" href="#" style="top:282px;left:0;width:112px;height:36px">Contact Us</a>
  </div>
  <div class="img-fill map" role="img" aria-label="Map of the Philippines marking centres in Baguio, Manila, Batangas, Bacolod and Davao"></div>
</section>

<section class="offer">
  <div class="offer-card" style="left:161px"><div class="icon"></div><h3>What We Do</h3><p>Our company has been established in the Philippines for over 20 years...</p></div>
  <div class="offer-card" style="left:470px"><div class="icon"></div><h3>How We Help</h3><p>We work with companies to find skilled workers that meet the UK requirements for Visas...</p></div>
  <div class="offer-card" style="left:779px"><div class="icon"></div><h3>Where To Start</h3><p>We need to know what your issues are and how we can understand the personnal you...</p></div>
  <a class="btn" href="#" style="left:543px;top:419px;width:113px;height:35px">Contact Us</a>
</section>

<section class="placement">
  <h2 class="center-title" style="top:82px">Placement We Provide In</h2>
  <div class="slider-arrow" style="left:98px"><svg width="14" height="10"><path d="M13 5H1M5 1L1 5l4 4" stroke="#999" fill="none"/></svg></div>
  <div class="tile" style="left:161px;background:linear-gradient(135deg,#9fb0c0,#5d7185)" role="img" aria-label="Nursing staff in a hospital ward">Nursing</div>
  <div class="tile" style="left:462px;background:linear-gradient(135deg,#8a8a7c,#4f5a4a 60%,#b58a3a)" role="img" aria-label="Engineers in hard hats on site">Engineering</div>
  <div class="tile" style="left:765px;background:linear-gradient(135deg,#7d8a80,#3f4a45)" role="img" aria-label="Welders at work in a workshop">Welding</div>
  <div class="slider-arrow" style="left:1059px"><svg width="14" height="10"><path d="M1 5h12M9 1l4 4-4 4" stroke="#999" fill="none"/></svg></div>
  <a class="btn" href="#" style="left:547px;top:433px;width:106px;height:34px">View All</a>
</section>

<section class="testimonial">
  <div class="img-fill photo" role="img" aria-label="Female engineer in a white hard hat standing in a modern building"></div>
  <div class="quote-card">
    <div class="stars">★★★★★</div>
    <p>Lorem ipsum dolor sit amet, consectetur adipiscing elit, sed do eiusmod tempor incididunt ut labore et dolore magna aliqua. Ut enim ad minim veniam, quis nostrud exercitation ullamco laboris nisi...</p>
    <div class="name">Maren Holt</div>
    <div class="role">Engineer</div>
    <div class="qmark">&#8220;</div>
  </div>
</section>

<section class="articles">
  <div class="article-card" style="left:161px"><span class="badge"></span><h3>UK Skilled Workers List</h3><p>The UK government since brexit have developed a new system based on points (similar to Australia)...</p><a class="btn" href="#">Read More</a></div>
  <div class="article-card" style="left:464px"><span class="badge"></span><h3>Sponsor Licence</h3><p>If you have areas of your business that meet the entry requirements of skilled labour your next...</p><a class="btn" href="#">Read More</a></div>
  <div class="article-card" style="left:767px"><span class="badge"></span><h3>Recruitment Timeline</h3><p>Brief us on the job profiles – this is passed on to our teams in the Philippines...</p><a class="btn" href="#">Read More</a></div>
</section>

<section class="contact-band">
  <div class="img-fill photo" role="img" aria-label="Two smiling engineers in hard hats holding a tablet and folder"></div>
  <div class="copy">
    <h2>Contact Us Today</h2>
    <div class="rule"></div>
    <p>Please contact us today with your requirements, this can be care workers, chef, welders, pipe fitters, caravan cabinet makers, medical workers. The UK list of required skills is extensive and the Philippines offersenglish speaking highly qualified hard working employees. Contact us today and make that first step to a highly motivated , quality skilled workforce.</p>
    <a class="btn white" href="#" style="left:0;top:298px;width:113px;height:36px">Contact Us</a>
  </div>
</section>

<section class="quick-contact">
  <h2 class="center-title" style="top:90px;font-size:30px">Quick Contact</h2>
  <div class="qc-field" style="left:295px;top:184px"><div class="lbl">First Name</div><div class="val">Daniel</div><svg width="16" height="16"><circle cx="8" cy="5" r="3.5" stroke="#999" fill="none"/><path d="M2 15c0-4 12-4 12 0z" stroke="#999" fill="none"/></svg></div>
  <div class="qc-field" style="left:615px;top:184px"><div class="lbl">Last Name</div><div class="val">Reyes</div><svg width="16" height="16"><circle cx="8" cy="5" r="3.5" stroke="#999" fill="none"/><path d="M2 15c0-4 12-4 12 0z" stroke="#999" fill="none"/></svg></div>
  <div class="qc-field" style="left:295px;top:268px"><div class="lbl">Phone</div><div class="val">123 456 7890</div><svg width="16" height="16"><path d="M3 1l3 3-2 2c1 3 3 5 6 6l2-2 3 3-2 2C7 15 1 9 1 3z" stroke="#999" fill="none"/></svg></div>
  <div class="qc-field" style="left:615px;top:268px"><div class="lbl">Email</div><div class="val">info@danielreyes.example.com</div><svg width="18" height="14"><rect x="1" y="1" width="16" height="12" stroke="#999" fill="none"/><path d="M1 1l8 7 8-7" stroke="#999" fill="none"/></svg></div>
  <div class="qc-field" style="left:295px;top:352px;width:610px;height:82px"><div class="lbl">Message</div><div class="val">Type Your Message</div><svg width="18" height="16"><path d="M2 2h11v8H7l-3 3v-3H2z" stroke="#999" fill="none"/><path d="M15 5h2v8h-2v3l-3-3H8" stroke="#999" fill="none"/></svg></div>
  <a class="btn" href="#" style="left:543px;top:476px;width:114px;height:34px">Submit Now</a>
</section>

<footer class="site-footer">
  <div class="foot-col" style="left:161px">
    <h4>Quick Links</h4><div class="rule"></div>
    <div class="links"><span>› Home</span><span>› Articles</span><span>› About</span><span>› Training</span><span>› Services</span><span>› Contact Us</span></div>
  </div>
  <div class="foot-col" style="left:441px">
    <h4>Contact Details</h4><div class="rule"></div>
    <div class="contact-list">
      <div><svg width="12" height="16"><path d="M6 15C2 10 1 8 1 6a5 5 0 0110 0c0 2-1 4-5 9z" fill="#fff"/><circle cx="6" cy="6" r="2" fill="#0054aa"/></svg><span>Larkfield Court, Brindle Road, Elmsworth<br>EL4 2 United Kingdom</span></div>
      <div><svg width="14" height="14"><path d="M3 1l3 3-2 2c1 2 2 3 4 4l2-2 3 3-2 2C6 13 1 8 1 3z" fill="#fff"/></svg><span>07700900412</span></div>
      <div><svg width="16" height="12"><rect width="16" height="12" fill="#fff"/><path d="M0 0l8 6 8-6" stroke="#0054aa" fill="none"/></svg><span>sales@trellanstaffing.example.com</span></div>
    </div>
  </div>
  <div class="foot-col" style="left:799px">
    <h4>Follow Us On:</h4><div class="rule"></div>
    <div class="socials"><span></span><span></span><span></span><span></span></div>
    <div class="foot-brand"><span class="mark"></span>Trellan Staffing</div>
  </div>
</footer>
<div class="legal">© 2023 Trellan Staffing Ltd. All Rights Reserved</div>

</body>
</html>
```